Business Card Design for a Personal Trainer

I need a business card design for my job as a personal trainer. It should have a unique, modern and exclusive design. On the front there should be only my logo with my name and my job. 0162/3819204 Tobias Lendhart Wiesengrundweg 14 80417 Munich Germany The most important contact information is the web adress. it can be bigger than the rest, but its not necessary. The card should be 8,5cmx5,5cm big. Font: Roboto. Colors: black, white, gray, 56c1ff.

```html
<!DOCTYPE html>
<html lang="de">
<head>
<meta charset="utf-8">
<title>Tobias Lendhart – Personal Trainer Visitenkarte</title>
<link rel="stylesheet" href="https://fonts.googleapis.com/css2?family=Roboto:wght@300;400;500;700;900&display=swap">
<style>
  :root {
    --brand-blue: #56c1ff;
    --brand-blue-deep: #3fb3f7;
    --ink: #111111;
    --gray: #7a7a7a;
    --light-gray: #e8e8e8;
    --paper: #ffffff;
    --backdrop: #5a5a5a;
  }
  * { box-sizing: border-box; margin: 0; padding: 0; }
  html, body {
    width: 1200px; height: 1200px; overflow: hidden;
    background: radial-gradient(circle at 50% 45%, #8a8a8a 0%, var(--backdrop) 70%);
    font-family: "Roboto", sans-serif;
  }
  .stage { position: relative; width: 1200px; height: 1200px; }

  .card {
    position: absolute; left: 200px; width: 800px; height: 518px;
    overflow: hidden; box-shadow: 0 18px 40px rgba(0,0,0,.35);
  }

  /* Logo side */
  .card-logo-side {
    top: 64px;
    background: linear-gradient(135deg, var(--brand-blue) 0%, var(--brand-blue-deep) 100%);
  }
  .card-logo-side .frame {
    position: absolute; inset: 30px;
    border: 3px solid var(--light-gray);
  }
  .brand-lockup {
    position: absolute; left: 0; right: 0; top: 170px;
    display: flex; flex-direction: column; align-items: center;
    color: var(--light-gray);
  }
  .brand-name-row { display: flex; align-items: center; gap: 18px; }
  .brand-square { width: 34px; height: 34px; background: var(--light-gray); }
  .brand-name {
    font-weight: 300; font-size: 54px; letter-spacing: 2px; line-height: 1;
  }
  .brand-role {
    display: flex; align-items: center; gap: 12px; margin-top: 12px;
    font-weight: 300; font-size: 17px; letter-spacing: 9px;
  }
  .brand-role::before, .brand-role::after {
    content: ""; width: 70px; height: 2px; background: var(--light-gray);
  }
  .back-web {
    position: absolute; left: 50%; bottom: 14px; transform: translateX(-50%);
    padding: 0 14px; background: var(--brand-blue-deep);
    font-weight: 700; font-size: 30px; color: var(--paper); white-space: nowrap;
  }
  .back-web .web-affix { color: var(--ink); }

  /* Contact side */
  .card-contact-side { top: 618px; background: var(--paper); }
  .contact-name {
    position: absolute; left: 44px; top: 34px;
    font-weight: 700; font-size: 62px; line-height: 1; white-space: nowrap;
  }
  .contact-name .first { color: var(--brand-blue); }
  .contact-name .last { color: var(--gray); }
  .address {
    position: absolute; left: 46px; top: 124px;
    font-weight: 700; font-size: 20px; line-height: 1.3; color: var(--ink);
  }
  .contact-lines {
    position: absolute; left: 46px; top: 200px;
    display: flex; flex-direction: column; gap: 8px;
    font-weight: 400; font-size: 21px; color: var(--ink);
  }
  .contact-line { display: flex; align-items: center; gap: 10px; }
  .contact-line svg { width: 22px; height: 22px; flex: none; }
  .front-web {
    position: absolute; left: 46px; bottom: 54px; z-index: 2;
    font-weight: 700; font-size: 34px; color: var(--brand-blue); white-space: nowrap;
  }
  .front-web .web-affix { color: var(--ink); }
  .accent-band {
    position: absolute; bottom: 0; height: 26px; background: var(--brand-blue);
  }
  .accent-band.left { left: 0; width: 460px; }
  .accent-band.right { right: 0; width: 60px; }
  .portrait {
    position: absolute; left: 480px; top: 170px; width: 260px; height: 348px;
    background: linear-gradient(180deg, #6c6c6c 0%, #2c2c2c 100%);
  }
</style>
</head>
<body>
<main class="stage">

  <section class="card card-logo-side" aria-label="Vorderseite">
    <div class="frame"></div>
    <div class="brand-lockup">
      <div class="brand-name-row">
        <span class="brand-square"></span>
        <span class="brand-name">TOBIAS LENDHART</span>
      </div>
      <div class="brand-role">PERSONAL TRAINER</div>
    </div>
    <div class="back-web"><span class="web-affix">www.</span>tobiaslendhart<span class="web-affix">.de</span></div>
  </section>

  <section class="card card-contact-side" aria-label="Rückseite">
    <h1 class="contact-name"><span class="first">Tobias</span> <span class="last">Lendhart</span></h1>
    <p class="address">Wiesengrundweg 14<br>80417 München</p>
    <div class="contact-lines">
      <div class="contact-line">
        <svg viewBox="0 0 24 24" fill="none" stroke="#56c1ff" stroke-width="2"><circle cx="12" cy="12" r="10"/><path d="M8.5 7.5c0 4.5 3.5 8.5 8 9l1-2-2.5-1.2-1.2 1.1c-1.5-.7-2.7-2-3.3-3.4l1.1-1.2L10.5 7.3z" fill="#56c1ff" stroke="none"/></svg>
        <span>0162/3819204</span>
      </div>
      <div class="contact-line">
        <svg viewBox="0 0 24 24" fill="none" stroke="#56c1ff" stroke-width="2"><circle cx="12" cy="12" r="10"/><rect x="7" y="8.5" width="10" height="7" stroke-width="1.6"/><path d="M7 8.5l5 4 5-4" stroke-width="1.6"/></svg>
        <span>t.lendhart@kontakt-mail.de</span>
      </div>
    </div>
    <div class="front-web"><span class="web-affix">www.</span>tobiaslendhart<span class="web-affix">.de</span></div>
    <div class="accent-band left"></div>
    <div class="portrait" role="img" aria-label="Schwarzweiß-Porträt des Trainers mit verschränkten Armen"></div>
    <div class="accent-band right"></div>
  </section>

</main>
</body>
</html>
```